New word press website site design

We provide email marketing to aircraft brokers and dealers to assist in finding buyers for their aircraft.

Our target market to purchase our broadcasts are the aircraft sellers – NOT the buyers.

Our target market when sending the email broadcast, are the buyers (end users).

The website should target brokers and our email database targets the buyers.

We do not buy or sell aircraft as a company. We provide email marketing solutions to connect buyers and sellers of aircraft.

Our other site is planelantern.com and will be redesigned soon. Please use it as a reference as far as general scope but they layout can be completely different and should include helicopters only as far as imagery. The colors should be similar as the logos are similar, however we do NOT want both sites to be identical in use of primary color

Plenty of images and sample broadcasts attached to use as needed throughout the site.

Headlines listed below with some text copy.

In the event that we need to add more text, please use standard greek text as a place holder for the purposes of the mockup design.

Need to have a “SUBSCRIBE” button to join our mailing list.

Possible Headlines:

Exclusively Showcasing Rotor Wing Aircraft to the Global Marketplace

Showcasing Pre-Owned Helicopters Available For Sale, Lease, Trade, or Wanted for Acquisition.

Mobile-optimized Email Campaigns that Render Correctly Across all Devices

Targeted worldwide recipients that currently own, operate, or have an interest in rotor wing aircraft

STRONGEST Rotor Wing Database in the Industry

Text/Copy:

HOME
Rotorbay Vista is one of most powerful marketing tools in the industry to utilize in reaching targeted buyers of pre-owned helicopters. Rotorbay Vista provides the rotor wing aircraft market with a fast, effective, and affordable email broadcast solution to utilize in the marketing of Helicopters for sale.

Developed Exclusively to Showcase Rotor Wing Aircraft to the Global marketplace, Rotorbay Vista is a powerful tool designed to maximize leads and accelerate the sales process by providing the ability to reach a global network of Helicopter buyers in a matter of seconds.

DATABASE:

While Rotorbay Vista is delivered to all known broker/dealers, our primary focus is in reaching end users. Our opt-in/opt-out recipient database is updated daily and developed specifically to deliver the latest details on helicopters available for sale or lease to the inboxes of a global network of Helicopter buyers and sellers.

· Helicopter Owners

· Helicopter Operators

· Helicopter Charter Services

· Helicopter Management Companies

· Corporate/Municipal Flight Departments

· Helicopter Pilots

· Senior Aviation Executives

· Wealth Management Firms

· High Net Worth Individuals

· Helicopter Broker/Dealers

Helicopter Tour/Travel Firms

· Off Shore Oil & Gas Production Firms

· Municipalities/Media/Medevac Firms

Our recipient database is continuously updated and developed specifically to reach buyers and sellers of Helicopters. This ensures that your Helicopter will be showcased to the right people. Rotorbay Vista does not broadcast non-rotor wing aircraft and focuses exclusively on the Global Helicopter Market.

Broadcast Design:

Rotorbay Vista broadcast ads are custom designed for you by incorporating your corporate image and branding. Because you have worked hard in developing your corporate image, we strive to maintain it while designing an ad that will showcase your Helicopter to its best advantage. Rotorbay Vista utilizes Mobile-optimized Email Campaigns with Responsive Coding to render correctly across all devices

Once you have approved the design, we schedule the broadcast to be sent on the available date and time you request. The broadcast will link to your website and the results can be immediate. All email leads and replies will go to the email address that you provided.

Pricing:
Create a place holder for 3 Different Broadcast Packages

-Broadcast Package A
-Broadcast Package B
-Broadcast Package C

Target Market(s)

The target market is any person or company that has aircraft for sale. We work with brokers, dealers, and owners to assist in finding buyers for their aircraft using email marketing campaigns (Showcase broadcasts).

Industry/Entity Type

Aviation

Colors
0255a3
00a990

Requirements
Nice to have
• Samples of helicopter for sale broadcast ads in /image gallery/slider

```html
<!DOCTYPE html>
<html lang="en">
<head>
<meta charset="utf-8">
<title>Rotorbay Vista</title>
<link rel="stylesheet" href="https://fonts.googleapis.com/css2?family=Roboto:wght@400;500;700;900&display=swap">
<style>
:root{
  --navy:#112a4b;
  --navy-deep:#0e233f;
  --green:#77bf43;
  --green-dark:#5ea52f;
  --red:#e0201b;
  --ink:#222;
  --text:#555;
  --muted:#777;
  --light:#f2f2f2;
  --white:#fff;
}
*{box-sizing:border-box;margin:0;padding:0}
html,body{width:1200px;height:2946px;overflow:hidden}
body{font-family:'Roboto',sans-serif;color:var(--text);background:var(--white);position:relative}
.abs{position:absolute}

/* header */
.site-header{position:absolute;left:0;top:0;width:1200px;height:79px;background:var(--white)}
.brand{position:absolute;left:220px;top:22px;display:flex;align-items:center;gap:8px;font-size:22px;font-weight:700;color:var(--navy);font-family:'Roboto',sans-serif}
.brand-dot{width:14px;height:14px;border-radius:50%;background:var(--green)}
.main-nav{position:absolute;left:448px;top:31px;display:flex;gap:20px;font-size:13px;color:var(--ink)}
.main-nav a{color:inherit;text-decoration:none;padding-bottom:6px}
.main-nav a.active{color:var(--green);border-bottom:3px solid var(--green)}
.header-phone{position:absolute;left:800px;top:31px;font-size:13px;color:var(--ink);display:flex;align-items:center;gap:6px;font-weight:500}
.btn{display:inline-block;background:var(--green);color:var(--white);font-weight:700;font-size:11px;text-transform:uppercase;text-align:center;text-decoration:none}
.header-subscribe{position:absolute;left:902px;top:25px;width:78px;height:28px;line-height:28px}

/* hero */
.hero{position:absolute;left:0;top:79px;width:1200px;height:453px;background:linear-gradient(180deg,#6d7f95 0%,#c9a46a 55%,#e3a24a 62%,#3f4a2c 72%,#2b321f 100%)}
.hero h1{position:absolute;left:0;top:192px;width:1200px;text-align:center;color:var(--white);font-size:27px;font-weight:700;line-height:32px;text-shadow:0 1px 3px rgba(0,0,0,.5)}
.hero-dots{position:absolute;left:548px;top:430px;display:flex;gap:6px}
.hero-dots span{width:18px;height:3px;background:var(--white)}
.hero-dots span.on{background:var(--green)}

/* welcome */
.welcome{position:absolute;left:0;top:532px;width:1200px;height:613px}
.section-title{font-size:26px;font-weight:700;color:var(--ink);text-align:center}
.welcome .section-title{position:absolute;left:0;top:50px;width:1200px}
.welcome-band{position:absolute;left:0;top:260px}
.video{position:absolute;left:220px;top:106px;width:760px;height:320px;background:radial-gradient(ellipse at 55% 45%,#4a4f57 0%,#1c1e22 45%,#050505 80%)}
.video-caption{position:absolute;left:12px;bottom:6px;font-size:42px;font-weight:900;color:rgba(255,255,255,.12);letter-spacing:1px}
.play{position:absolute;left:352px;top:132px}
.welcome-copy{position:absolute;top:478px;width:375px;font-size:12px;line-height:18px;color:#dfe4ea}
.welcome-copy.left{left:228px}
.welcome-copy.right{left:640px;width:345px}

/* services */
.services{position:absolute;left:0;top:1145px;width:1200px;height:648px;background:linear-gradient(90deg,#f4f4f4,#ececec)}
.services-deco{position:absolute;left:920px;top:0;width:280px;height:400px;background:linear-gradient(160deg,rgba(200,200,200,.35),rgba(240,240,240,0))}
.services .section-title{position:absolute;left:0;top:48px;width:1200px}
.services-intro{position:absolute;left:290px;top:92px;width:620px;text-align:center;font-size:12px;line-height:18px;color:var(--muted)}
.services-photo{position:absolute;left:220px;top:167px;width:501px;height:332px;background:linear-gradient(180deg,#cfdbe9 0%,#8fa8c6 45%,#3d5f8e 100%)}
.audience{position:absolute;left:721px;top:167px;width:259px;height:332px;background:var(--green);padding:18px 0 0 20px;list-style:none}
.audience li{display:flex;align-items:center;gap:8px;font-size:11px;color:var(--white);height:22.6px}
.services-note{position:absolute;left:290px;top:527px;width:620px;text-align:center;font-size:12px;line-height:17px;color:var(--muted)}

/* broadcast design */
.design{position:absolute;left:0;top:1793px;width:1200px;height:289px;background:var(--white)}
.design-shapes{position:absolute;left:0;top:0}
.sample{position:absolute;border:2px solid #111}
.sample.one{left:216px;top:-20px;width:236px;height:250px;background:linear-gradient(180deg,#1a1a1a 0%,#c91f1f 22%,#2b2b2b 45%,#7a8a9c 70%,#111 100%)}
.sample.two{left:412px;top:62px;width:200px;height:172px;background:linear-gradient(180deg,#1d1d1d 0%,#1d1d1d 42%,#c9ced4 60%,#2a2a2a 100%)}
.design h2{position:absolute;left:674px;top:52px;font-size:24px;font-weight:700;color:var(--ink)}
.design p{position:absolute;left:674px;top:92px;width:302px;font-size:12px;line-height:18px;color:var(--muted)}
.design .btn{position:absolute;left:674px;top:210px;width:162px;height:26px;line-height:26px;font-size:11px}

/* pricing */
.pricing{position:absolute;left:0;top:2082px;width:1200px;height:618px;background:linear-gradient(90deg,#f3f3f3,#fafafa 50%,#f3f3f3)}
.pricing .section-title{position:absolute;left:0;top:45px;width:1200px}
.pricing-sub{position:absolute;left:0;top:84px;width:1200px;text-align:center;font-size:11px;color:var(--muted)}
.plan{position:absolute;top:157px;width:253px;height:412px;background:var(--white)}
.plan.a{left:220px}
.plan.b{left:473px;top:137px;height:452px;box-shadow:0 0 12px rgba(0,0,0,.15);z-index:2}
.plan.c{left:726px;width:254px}
.plan-head{height:65px;background:var(--navy);color:var(--white);font-size:19px;text-align:center;line-height:65px;font-weight:400}
.plan-head b{font-weight:700}
.plan.b .plan-head{height:85px;line-height:105px;background:var(--green)}
.plan-price{height:66px;background:var(--navy-deep);color:var(--white);font-size:23px;font-weight:700;text-align:center;line-height:66px}
.plan-list{list-style:none;padding:14px 22px 0}
.plan-list li{font-size:11px;color:var(--text);height:31px;line-height:31px;border-bottom:1px solid #eee}
.plan .btn{position:absolute;left:27px;bottom:24px;width:199px;height:39px;line-height:39px}
.plan.b .btn{bottom:44px}
.badge{position:absolute;left:78px;top:-12px;width:96px;height:24px;border-radius:12px;background:var(--red);color:var(--white);font-size:9px;font-weight:700;text-align:center;line-height:24px}

/* footer */
.site-footer{position:absolute;left:0;top:2700px;width:1200px;height:246px;background:var(--navy);color:#c8d0da;font-size:11px;line-height:17px}
.footer-col{position:absolute;top:54px}
.footer-col h4{font-size:10px;font-weight:700;color:var(--white);text-transform:uppercase;margin-bottom:8px}
.footer-col ul{list-style:none}
.col-contact{left:220px}
.col-quick{left:428px}
.col-help{left:589px}
.col-sub{left:738px}
.signup{display:flex;width:242px;height:33px;background:var(--white);margin-top:2px}
.signup span{flex:1;padding-left:12px;line-height:33px;color:#aaa;font-size:11px}
.signup .btn{width:86px;height:29px;line-height:29px;margin:2px}
.social{display:flex;gap:9px;margin-top:20px}
.social span{width:24px;height:24px;background:#6b7a8e}
.footer-rule{position:absolute;left:0;top:194px;width:1200px;height:1px;background:rgba(255,255,255,.1)}
.copyright{position:absolute;left:0;top:218px;width:1200px;text-align:center;font-size:11px}
</style>
</head>
<body>

<header class="site-header">
  <div class="brand"><span class="brand-dot"></span>Rotorbay Vista</div>
  <nav class="main-nav">
    <a class="active">Home</a><a>Services</a><a>Broadcast Design</a><a>Pricing</a><a>Contact</a>
  </nav>
  <div class="header-phone">
    <svg width="12" height="12" viewBox="0 0 24 24"><path fill="#222" d="M6.6 10.8a15 15 0 006.6 6.6l2.2-2.2c.3-.3.7-.4 1-.2 1.1.4 2.3.6 3.6.6.6 0 1 .4 1 1V20c0 .6-.4 1-1 1A17 17 0 013 4c0-.6.4-1 1-1h3.5c.6 0 1 .4 1 1 0 1.3.2 2.5.6 3.6.1.3 0 .7-.2 1z"/></svg>
    1800 555 014
  </div>
  <a class="btn header-subscribe">Subscribe</a>
</header>

<section class="hero" role="img" aria-label="Helicopter on a grass airfield silhouetted against a sunset sky">
  <h1>Exclusively Showcasing Rotor Wing Aircraft<br>to the Global Marketplace</h1>
  <div class="hero-dots"><span class="on"></span><span></span><span></span><span></span><span></span></div>
</section>

<section class="welcome">
  <h2 class="section-title">Welcome Rotorbay Vista</h2>
  <svg class="welcome-band" width="1200" height="353" viewBox="0 0 1200 353">
    <path d="M0 8 Q600 -14 1200 8 L1200 353 L0 353 Z" fill="#112a4b"/>
    <path d="M0 0 Q300 22 600 22 Q900 22 1200 0 L1200 8 Q600 -14 0 8Z" fill="#fff"/>
  </svg>
  <div class="video" role="img" aria-label="Promotional video still of a silver helicopter on a dark stage">
    <div class="video-caption">ROTORBAY VISTA</div>
    <svg class="play" width="56" height="56" viewBox="0 0 56 56"><circle cx="28" cy="28" r="25" fill="none" stroke="#fff" stroke-width="3"/><path d="M22 17 L39 28 L22 39Z" fill="#fff"/></svg>
  </div>
  <p class="welcome-copy left">Rotorbay Vista is one of most powerful marketing tools in the industry to utilize in reaching targeted buyers of pre-owned helicopters. Rotorbay Vista provides the rotor wing aircraft market with a fast, effective, and affordable email broadcast solution to utilize in the marketing of Helicopters for sale.</p>
  <p class="welcome-copy right">Developed Exclusively to Showcase Rotor Wing Aircraft to the Global marketplace, Rotorbay Vista is a powerful tool designed to maximize leads and accelerate the sales process by providing the ability to reach a global network of Helicopter buyers in a matter of seconds.</p>
</section>

<section class="services">
  <div class="services-deco" role="img" aria-label="Faint helicopter photograph fading into the background"></div>
  <h2 class="section-title">What Services We offer</h2>
  <p class="services-intro">Rotorbay Vista is one of most powerful marketing tools in the industry to utilize in reaching targeted buyers of pre-owned helicopters. Rotorbay Vista provides the rotor wing aircraft market with a fast, effective, and affordable email broadcast solution to utilize in the marketing of Helicopters for sale.</p>
  <div class="services-photo" role="img" aria-label="Two dark helicopters flying in front of snowy mountains"></div>
  <ul class="audience">
    <li><svg width="10" height="10" viewBox="0 0 10 10"><path d="M1 5 L4 8 L9 2" stroke="#fff" stroke-width="2" fill="none"/></svg>Helicopter Owners</li>
    <li><svg width="10" height="10" viewBox="0 0 10 10"><path d="M1 5 L4 8 L9 2" stroke="#fff" stroke-width="2" fill="none"/></svg>Helicopter Operators</li>
    <li><svg width="10" height="10" viewBox="0 0 10 10"><path d="M1 5 L4 8 L9 2" stroke="#fff" stroke-width="2" fill="none"/></svg>Helicopter Charter Services</li>
    <li><svg width="10" height="10" viewBox="0 0 10 10"><path d="M1 5 L4 8 L9 2" stroke="#fff" stroke-width="2" fill="none"/></svg>Helicopter Management Companies</li>
    <li><svg width="10" height="10" viewBox="0 0 10 10"><path d="M1 5 L4 8 L9 2" stroke="#fff" stroke-width="2" fill="none"/></svg>Corporate/Municipal Flight Departments</li>
    <li><svg width="10" height="10" viewBox="0 0 10 10"><path d="M1 5 L4 8 L9 2" stroke="#fff" stroke-width="2" fill="none"/></svg>Helicopter Pilots</li>
    <li><svg width="10" height="10" viewBox="0 0 10 10"><path d="M1 5 L4 8 L9 2" stroke="#fff" stroke-width="2" fill="none"/></svg>Senior Aviation Executives</li>
    <li><svg width="10" height="10" viewBox="0 0 10 10"><path d="M1 5 L4 8 L9 2" stroke="#fff" stroke-width="2" fill="none"/></svg>Wealth Management Firms</li>
    <li><svg width="10" height="10" viewBox="0 0 10 10"><path d="M1 5 L4 8 L9 2" stroke="#fff" stroke-width="2" fill="none"/></svg>High Net Worth Individuals</li>
    <li><svg width="10" height="10" viewBox="0 0 10 10"><path d="M1 5 L4 8 L9 2" stroke="#fff" stroke-width="2" fill="none"/></svg>Helicopter Broker/Dealers</li>
    <li><svg width="10" height="10" viewBox="0 0 10 10"><path d="M1 5 L4 8 L9 2" stroke="#fff" stroke-width="2" fill="none"/></svg>Helicopter Tour/Travel Firms</li>
    <li><svg width="10" height="10" viewBox="0 0 10 10"><path d="M1 5 L4 8 L9 2" stroke="#fff" stroke-width="2" fill="none"/></svg>Off Shore Oil &amp; Gas Production Firms</li>
    <li><svg width="10" height="10" viewBox="0 0 10 10"><path d="M1 5 L4 8 L9 2" stroke="#fff" stroke-width="2" fill="none"/></svg>Municipalities/Media/Medevac Firms</li>
  </ul>
  <p class="services-note">Our recipient database is continuously updated and developed specifically to reach buyers and sellers of Helicopters. This ensures that your Helicopter will be showcased to the right people. Rotorbay Vista does not broadcast non-rotor wing aircraft and focuses exclusively on the Global Helicopter Market.</p>
</section>

<section class="design">
  <svg class="design-shapes" width="1200" height="289" viewBox="0 0 1200 289">
    <path d="M0 0 L430 0 L0 250Z" fill="#112a4b"/>
    <path d="M0 289 L190 120 L250 289Z" fill="#77bf43"/>
    <path d="M560 289 L600 180 L680 289Z" fill="#77bf43"/>
    <path d="M300 289 L640 0 L1200 0 L1200 40 L760 289Z" fill="#f1f1f1"/>
  </svg>
  <div class="sample one" role="img" aria-label="Sample broadcast ad for a helicopter for sale with photos and specifications"></div>
  <div class="sample two" role="img" aria-label="Sample broadcast ad for a helicopter wanted for acquisition"></div>
  <h2>Broadcast Design</h2>
  <p>Rotorbay Vista is one of most powerful marketing tools in the industry to utilize in reaching targeted buyers of pre-owned helicopters. Rotorbay Vista provides the rotor wing aircraft market with a fast, effective, and affordable email broadcast solution to utilize in the marketing of Helicopters for sale.</p>
  <a class="btn">Receive a Design Proof</a>
</section>

<section class="pricing">
  <h2 class="section-title">3 Different Broadcast Packages</h2>
  <p class="pricing-sub">Our Broadcast Packages Pricing below listed:</p>

  <div class="plan a">
    <div class="plan-head">Broadcast <b>Package A</b></div>
    <div class="plan-price">$39.99</div>
    <ul class="plan-list">
      <li>01. Awesome lorem ipsum dolor sit</li><li>02. Awesome lorem ipsum dolor sit</li><li>03. Awesome lorem ipsum dolor sit</li><li>04. Awesome lorem ipsum dolor sit</li><li>05. Awesome lorem ipsum dolor sit</li><li>06. Awesome lorem ipsum dolor sit</li>
    </ul>
    <a class="btn">Select Package</a>
  </div>

  <div class="plan b">
    <div class="badge">MOST POPULAR</div>
    <div class="plan-head">Broadcast <b>Package B</b></div>
    <div class="plan-price">$39.99</div>
    <ul class="plan-list">
      <li>01. Awesome lorem ipsum dolor sit</li><li>02. Awesome lorem ipsum dolor sit</li><li>03. Awesome lorem ipsum dolor sit</li><li>04. Awesome lorem ipsum dolor sit</li><li>05. Awesome lorem ipsum dolor sit</li><li>06. Awesome lorem ipsum dolor sit</li>
    </ul>
    <a class="btn">Select Package</a>
  </div>

  <div class="plan c">
    <div class="plan-head">Broadcast <b>Package C</b></div>
    <div class="plan-price">$39.99</div>
    <ul class="plan-list">
      <li>01. Awesome lorem ipsum dolor sit</li><li>02. Awesome lorem ipsum dolor sit</li><li>03. Awesome lorem ipsum dolor sit</li><li>04. Awesome lorem ipsum dolor sit</li><li>05. Awesome lorem ipsum dolor sit</li><li>06. Awesome lorem ipsum dolor sit</li>
    </ul>
    <a class="btn">Select Package</a>
  </div>
</section>

<footer class="site-footer">
  <div class="footer-col col-contact">
    <h4>Contact Info</h4>
    <p>228, lorem ipsum dolor,<br>dosis amet - 45895</p>
    <p style="margin-top:14px">T: 1800 555 0147<br>E: info@rotorbayvista.com</p>
  </div>
  <div class="footer-col col-quick">
    <h4>Quick Links</h4>
    <ul><li>Home</li><li>Services</li><li>Broadcast Design</li><li>Pricing</li><li>Contact</li></ul>
  </div>
  <div class="footer-col col-help">
    <h4>Helpful Links</h4>
    <ul><li>Terms of Use</li><li>Privacy Policy</li><li>Sitemap</li><li>Contact Us</li></ul>
  </div>
  <div class="footer-col col-sub">
    <h4>Subscribe to join our mailing list</h4>
    <div class="signup"><span>Email Address</span><a class="btn">Subscribe</a></div>
    <div class="social"><span></span><span></span><span></span><span></span></div>
  </div>
  <div class="footer-rule"></div>
  <p class="copyright">Copyright © 2018 Rotorbay Vista. All Rights Reserved</p>
</footer>

</body>
</html>
```